Product label for herbal salves, lotions, soaps and tinctures

We need a very simple, clean and organic looking label that can be used for an ointment jar, a lotion bottle and a dropper bottle.
We have an existing logo (see attached). We like the colors white, olive green, gold and black. It needs to include product name as dominant and logo. It also needs to include an ingredient list, and usage statement. Include weight of product, distributed by, made in the USA, and QVX statement.
Example of what needs to be present:
Logo
Name: Tranquil Ease Blend
Used for: For Muscle Aches, Arthritis, Tendonitis, Headaches
To Use: For muscle aches, arthritis and tendonitis, massage into affected area. For tension headache apply to neck, temples and forehead.
Store in a cool and dry place, away from direct heat and sunlight.
Weight of product: 1.75
DIST. BY: Copper Brook Herbal
Made in the USA
This product is not intended to diagnose, treat, cure
or prevent any disease. Not regulated
by the QVX. Please consult your health care practitioner
before using product. Discontinue use if any adverse reaction occurs.
Ingredient list:
Wildcrafted Ingredients:
Ashwagandha Root, Peppermint Leaf, Hops Flowers, St. John’s Wort Herb, Arnica Flowers, Green Tea Leaf, Alfalfa Leaf, Dandelion Root, Burdock Root, Chickweed Herb, Chaparral Leaf, Yarrow Flowers, Boneset Herb, Moringa Leaf, Meadowsweet Herb, Nettle Leaf
Organic Ingredients:
Olive Oil, Aloe Leaf, Sweet Birch Bark, Helichrysum Flowers, Holy Basil Leaf, Borage Herb, Ginger Root, Angelica Root, White Willow Bark, Mustard Seed, Beeswax, Vitamin E, Essential Oils
Dimensions of Jar:
Circumference: 7 in.
Height: 1 in.

```html
<!DOCTYPE html>
<html lang="en">
<head>
<meta charset="UTF-8">
<title>Copper Brook Herbal – Aloe Vera Label</title>
<link href="https://fonts.googleapis.com/css2?family=Noto+Sans:wght@400;600;700;800&display=swap" rel="stylesheet">
<style>
  :root {
    --stage: #c9d49c;
    --label-white: #eef5da;
    --label-white-soft: #e3ecca;
    --gold-band: #d3c587;
    --gold-band-deep: #c2b073;
    --olive: #5d6a24;
    --rule: rgba(93, 106, 36, 0.35);
    --ink: #141414;
    --ink-soft: #2b2b22;
  }
  * { margin: 0; padding: 0; box-sizing: border-box; }
  html, body {
    width: 1200px;
    height: 800px;
    overflow: hidden;
  }
  body {
    background: var(--stage);
    font-family: "Noto Sans", Arial, sans-serif;
    display: flex;
    align-items: center;
    justify-content: center;
    color: var(--ink);
  }
  .label {
    position: relative;
    width: 1120px;
    height: 640px;
    background: linear-gradient(180deg, var(--label-white-soft), var(--label-white));
    border-radius: 6px;
    overflow: hidden;
  }
  .label__band {
    position: absolute;
    left: 0;
    right: 0;
    top: 270px;
    bottom: 0;
    background: linear-gradient(135deg, var(--gold-band), var(--gold-band-deep));
  }
  .label__panels {
    position: absolute;
    inset: 0;
    display: grid;
    grid-template-columns: 350px 420px 350px;
  }
  .panel {
    position: relative;
    padding: 34px 28px 30px;
  }
  .panel--side + .panel--front,
  .panel--front + .panel--side {
    border-left: 1px solid var(--rule);
  }
  .panel__heading {
    font-size: 13px;
    font-weight: 700;
    letter-spacing: 1px;
    text-transform: uppercase;
    color: var(--olive);
    margin-bottom: 6px;
  }
  .panel__text {
    font-size: 12px;
    line-height: 1.5;
    color: var(--ink-soft);
    margin-bottom: 12px;
  }
  .panel__lower {
    position: absolute;
    left: 28px;
    right: 28px;
    top: 300px;
  }
  .panel__lower .panel__heading { color: var(--ink); }
  .panel--front {
    text-align: center;
  }
  .front__brand {
    margin-top: 84px;
    color: var(--olive);
    font-weight: 700;
    font-size: 34px;
    line-height: 1.1;
  }
  .front__name {
    position: absolute;
    left: 0;
    right: 0;
    top: 292px;
    font-size: 40px;
    font-weight: 800;
    letter-spacing: 0.5px;
  }
  .front__use {
    position: absolute;
    left: 0;
    right: 0;
    top: 356px;
    font-size: 21px;
    font-weight: 600;
    line-height: 1.3;
  }
  .front__weight {
    position: absolute;
    left: 0;
    right: 0;
    bottom: 34px;
    font-size: 17px;
    font-weight: 600;
  }
  .origin {
    position: absolute;
    left: 28px;
    right: 28px;
    bottom: 30px;
    font-size: 12px;
    line-height: 1.5;
    font-weight: 600;
  }
  .origin__made {
    font-weight: 800;
    letter-spacing: 1px;
    text-transform: uppercase;
  }
</style>
</head>
<body>
  <div class="label">
    <div class="label__band" role="img" aria-label="Engraved olive branch pattern with leaves and fruit in gold tones"></div>

    <div class="label__panels">
      <section class="panel panel--side panel--directions">
        <h2 class="panel__heading">To Use</h2>
        <p class="panel__text">For muscle aches, arthritis and tendonitis, massage into affected area. For tension headache apply to neck, temples and forehead.</p>
        <p class="panel__text">Store in a cool and dry place, away from direct heat and sunlight.</p>

        <div class="panel__lower">
          <h2 class="panel__heading">Please Note</h2>
          <p class="panel__text">This product is not intended to diagnose, treat, cure or prevent any disease. Not regulated by the QVX. Please consult your health care practitioner before using product. Discontinue use if any adverse reaction occurs.</p>
        </div>
      </section>

      <section class="panel panel--front">
        <div class="front__brand">Copper Brook Herbal</div>
        <h1 class="front__name">Aloe Vera</h1>
        <p class="front__use">For Muscle Aches, Arthritis,<br>Tendonitis, Headaches</p>
        <p class="front__weight">333 gm</p>
      </section>

      <section class="panel panel--side panel--ingredients">
        <h2 class="panel__heading">Wildcrafted Ingredients</h2>
        <p class="panel__text">Ashwagandha Root, Peppermint Leaf, Hops Flowers, St. John’s Wort Herb, Arnica Flowers, Green Tea Leaf, Alfalfa Leaf, Dandelion Root, Burdock Root, Chickweed Herb, Chaparral Leaf, Yarrow Flowers, Boneset Herb, Moringa Leaf, Meadowsweet Herb, Nettle Leaf</p>

        <div class="panel__lower">
          <h2 class="panel__heading">Organic Ingredients</h2>
          <p class="panel__text">Olive Oil, Aloe Leaf, Sweet Birch Bark, Helichrysum Flowers, Holy Basil Leaf, Borage Herb, Ginger Root, Angelica Root, White Willow Bark, Mustard Seed, Beeswax, Vitamin E, Essential Oils</p>
        </div>

        <div class="origin">
          <p>DIST. BY: Copper Brook Herbal</p>
          <p class="origin__made">Made in the USA</p>
        </div>
      </section>
    </div>
  </div>
</body>
</html>
```